professional business card design for technology company

We are a small technology consulting firm, specialising in consulting based around Cloud and Managed services. Our colour scheme is yellow, blue and white, as you can see in the logos. Although we are based in melbourne australia, due to the nature of our work, our clients can be located anywhere. We are looking for a clean, professional, positive look - similar to our company logo

Target Market(s)

small business

Industry/Entity Type

Business

Contact Information for Business Card

eye catching, designed to incorporate some level of raised printing. Must contain website address, phone number, name and job title

Requirements
Must have
• Logo (attached) - use of the same colour scheme

```html
<!DOCTYPE html>
<html lang="en">
<head>
<meta charset="utf-8">
<title>Orlenby Business Card</title>
<link rel="stylesheet" href="https://fonts.googleapis.com/css2?family=Exo+2:wght@400;500;700&display=swap">
<style>
  :root {
    --bg: #cfd0d1;
    --sky: #35a9e0;
    --paper: #f4f5f6;
    --ink: #2b2d30;
    --muted: #5b5e62;
    --rule: #55585c;
    --white: #ffffff;
  }
  * { margin: 0; padding: 0; box-sizing: border-box; }
  html, body { width: 1200px; height: 894px; overflow: hidden; }
  body {
    background: var(--bg);
    font-family: "Exo 2", sans-serif;
    position: relative;
  }
  .card {
    position: absolute;
    width: 560px;
    height: 320px;
    border-radius: 2px;
    overflow: hidden;
    box-shadow: 0 6px 18px rgba(0,0,0,0.18);
  }

  /* Front face */
  .card-front { left: 590px; top: 110px; background: var(--sky); }
  .brand-band {
    position: absolute;
    left: 290px; right: 0;
    top: 196px; height: 84px;
    background: var(--white);
    border-radius: 42px 0 0 42px;
    display: flex; align-items: center;
    padding-left: 40px; gap: 14px;
  }
  .brand-dot {
    width: 20px; height: 20px; border-radius: 50%;
    background: var(--sky);
    flex: none;
  }
  .brand-name {
    font-weight: 700; font-size: 38px; color: var(--muted);
    letter-spacing: -0.5px;
    white-space: nowrap;
  }

  /* Back face */
  .card-back { left: 50px; top: 470px; background: var(--paper); }
  .person { position: absolute; left: 36px; top: 28px; }
  .person-name { font-size: 22px; font-weight: 500; color: var(--sky); letter-spacing: 0.5px; }
  .person-title { font-size: 9px; color: var(--muted); letter-spacing: 1px; text-transform: uppercase; margin-top: 2px; }

  .contact-list { position: absolute; left: 36px; top: 90px; list-style: none; }
  .contact-list li { display: flex; height: 19px; align-items: center; }
  .contact-label { width: 66px; font-size: 13px; color: var(--sky); }
  .contact-value { font-size: 14px; color: var(--ink); letter-spacing: 0.8px; }

  .rule { position: absolute; height: 2px; background: var(--rule); }
  .rule-contact { left: 36px; top: 176px; width: 300px; }
  .rule-address { left: 36px; top: 222px; right: 0; }
  .rule-lower-1 { left: 36px; top: 262px; right: 0; }
  .rule-lower-2 { left: 36px; top: 286px; right: 0; }

  .address {
    position: absolute; left: 36px; top: 188px;
    display: flex; align-items: center; gap: 10px;
    font-size: 13px; color: var(--ink); letter-spacing: 1.2px;
  }
  .address svg { width: 14px; height: 20px; }

  .brand-tab {
    position: absolute;
    left: 400px; right: 0;
    top: 120px; height: 74px;
    background: var(--sky);
    border-radius: 37px 0 0 37px;
    display: flex; align-items: center; justify-content: center;
  }
  .brand-tab .brand-name { color: var(--white); font-size: 22px; }
</style>
</head>
<body>

  <section class="card card-front" aria-label="Card front">
    <div class="brand-band">
      <span class="brand-dot"></span>
      <span class="brand-name">Orlenby</span>
    </div>
  </section>

  <section class="card card-back" aria-label="Card back">
    <div class="person">
      <div class="person-name">Daniel Hart</div>
      <div class="person-title">General Manager</div>
    </div>

    <ul class="contact-list">
      <li><span class="contact-label">Phone:</span><span class="contact-value">014 276 5310</span></li>
      <li><span class="contact-label">Fax:</span><span class="contact-value">014 276 5310</span></li>
      <li><span class="contact-label">Email:</span><span class="contact-value">dhart@orlenby.com</span></li>
      <li><span class="contact-label">website</span><span class="contact-value">www.orlenby.com</span></li>
    </ul>

    <div class="rule rule-contact"></div>

    <div class="address">
      <svg viewBox="0 0 14 20" aria-hidden="true">
        <path d="M7 0C3.1 0 0 3.1 0 7c0 5 7 13 7 13s7-8 7-13C14 3.1 10.9 0 7 0z" fill="#35a9e0"/>
        <circle cx="7" cy="7" r="2.6" fill="#f4f5f6"/>
      </svg>
      <span>41, 9th floor, Harbour Line Road MLB</span>
    </div>

    <div class="rule rule-address"></div>
    <div class="rule rule-lower-1"></div>
    <div class="rule rule-lower-2"></div>

    <div class="brand-tab">
      <span class="brand-name">Orlenby</span>
    </div>
  </section>

</body>
</html>
```